Business Cards for IT Consulting Company (Managed Service Provider)

I am looking to have some business cards printed and would like some designs. We are an IT Consulting company based in Vancouver BC. I would like a nice clean and modern look to the cards. I have uploaded all the versions of my logo so parts can be used as needed. Here is a snippit from our website homepage:

Quillbrook Networks Ltd. is an IT Solutions Partner located in Vancouver BC, Canada. We offer IT solutions and support to customers in the greater Vancouver Area. With expertise in Microsoft platforms, as well as Linux and Mac OSX and over 12 years experience in the IT industry, Quillbrook Networks is dedicated to offering our clients top quality service and products. We take pride in the solutions we offer our customers. The greatest compliment a client can give us is to recommend our services.

Quillbrook Networks Ltd. offers a wide range of IT services from onsite service to remote support and managed service solutions. This allows clients to choose the support path that best suits their company’s needs. Supporting many different sized companies from small to enterprise level over the past 12 years Quillbrook Networks has the experience and expertise needed to ensure things run smoothly. Allowing our clients to focus on doing business.

Revolutionizing the way IT services are delivered.

Quillbrook Networks is dedicated to providing our clients with IT solutions that work and grow with them for years to come. This philosophy helps save money in the long run instead of replacing equipment constantly. Far too often IT solutions are not well thought out and while possibly solving the problem at hand, require replacement due to growth or quality within a very short time frame. Quillbrook Networks takes pride in providing solutions that will last and be able to accommodate growth without the need for replacement.

Industry/Entity Type

Information Technology

Contact Information for Business Card

Quillbrook Networks Ltd.
(Employee Name)
Eml: (Employees Email Address)
Web: quillbrook.me
Ph: 604-555-0148

Font styles to use
Serif
Sans Serif

Requirements
Must have
• The Company logo and company colors.
Nice to have
• - Our tag line: "Revolutionizing IT Services" or "Revolutionizing the way IT services are delivered."
• - Also I really like the idea of nature and technology together blending which is sort of where my logo came from so integrating that somehow onto the business cards would be great.

```html
<!DOCTYPE html>
<html lang="en">
<head>
<meta charset="utf-8">
<title>Quillbrook Networks Ltd. — Business Cards</title>
<link rel="stylesheet" href="https://fonts.googleapis.com/css2?family=Roboto:ital,wght@0,400;0,500;0,700;1,400&display=swap">
<style>
  :root {
    --backdrop: #a9a7a7;
    --card: #f4f4f4;
    --brand-blue: #1a8fd6;
    --brand-grey: #4a4a4c;
    --text: #454547;
    --white: #ffffff;
  }
  * { margin: 0; padding: 0; box-sizing: border-box; }
  html, body { width: 1200px; height: 1200px; overflow: hidden; }
  body {
    background: var(--backdrop);
    font-family: "Roboto", Arial, sans-serif;
    position: relative;
  }
  .card {
    position: absolute;
    background: var(--card);
    overflow: hidden;
  }
  .card--front { left: 238px; top: 118px; width: 724px; height: 420px; }
  .card--back  { left: 230px; top: 643px; width: 714px; height: 419px; }

  .brand {
    position: absolute;
    display: flex;
    align-items: center;
    gap: 18px;
    color: var(--brand-blue);
    font-weight: 500;
  }
  .brand__mark { background: var(--brand-blue); flex: none; }
  .brand__name { line-height: 1; }
  .brand__name span { display: block; }
  .brand__line1 { letter-spacing: 0.5px; }
  .brand__line2 { letter-spacing: 1px; margin-top: 6px; }

  .card--front .brand { left: 112px; top: 150px; }
  .card--front .brand__mark { width: 74px; height: 74px; }
  .card--front .brand__line1 { font-size: 58px; }
  .card--front .brand__line2 { font-size: 25px; }

  .tagline {
    position: absolute;
    left: 0; right: 0; top: 376px;
    display: flex;
    justify-content: center;
    align-items: center;
    gap: 16px;
    font-size: 18px;
    color: var(--text);
  }
  .tagline__rule {
    width: 110px; height: 3px;
    background: var(--brand-blue);
    border-radius: 2px;
  }

  .top-band {
    position: absolute;
    left: 0; top: 0;
    width: 100%; height: 124px;
    background: var(--brand-blue);
  }
  .top-rule {
    position: absolute;
    left: 0; top: 130px;
    width: 100%; height: 6px;
    background: var(--brand-grey);
  }

  .slogan {
    position: absolute;
    right: 39px; top: 30px;
    text-align: right;
    color: var(--white);
    font-size: 17.5px;
    line-height: 24.5px;
  }

  .card--back .brand { left: 33px; top: 166px; gap: 16px; }
  .card--back .brand__mark { width: 64px; height: 64px; }
  .card--back .brand__line1 { font-size: 50px; }
  .card--back .brand__line2 { font-size: 22px; }

  .contact {
    position: absolute;
    left: 54px; top: 288px;
    list-style: none;
    font-size: 17px;
    color: var(--text);
  }
  .contact li {
    display: flex;
    align-items: center;
    gap: 17px;
    height: 27px;
  }
  .contact svg { width: 16px; height: 16px; fill: var(--brand-blue); flex: none; }

  .person {
    position: absolute;
    right: 39px; top: 306px;
    text-align: right;
  }
  .person__name {
    color: var(--brand-blue);
    font-weight: 700;
    font-size: 25px;
  }
  .person__title {
    color: var(--text);
    font-style: italic;
    font-size: 16px;
    margin-top: 5px;
  }
</style>
</head>
<body>

<section class="card card--front" aria-label="Business card front">
  <div class="brand">
    <div class="brand__mark"></div>
    <div class="brand__name">
      <span class="brand__line1">Quillbrook</span>
      <span class="brand__line2">NETWORKS LTD.</span>
    </div>
  </div>
  <p class="tagline">
    <span class="tagline__rule"></span>
    Revolutionizing IT Services
    <span class="tagline__rule"></span>
  </p>
</section>

<section class="card card--back" aria-label="Business card back">
  <div class="top-band"></div>
  <div class="top-rule"></div>

  <p class="slogan">Revolutionizing the<br>way IT services<br>are delivered</p>

  <div class="brand">
    <div class="brand__mark"></div>
    <div class="brand__name">
      <span class="brand__line1">Quillbrook</span>
      <span class="brand__line2">NETWORKS LTD.</span>
    </div>
  </div>

  <ul class="contact">
    <li>
      <svg viewBox="0 0 16 16" aria-hidden="true"><path d="M2 6 C2 3 5 2 8 2 C11 2 14 3 14 6 L11 7 L10 5 H6 L5 7 Z M4 8 H12 L13 14 H3 Z"/></svg>
      604-555-0148
    </li>
    <li>
      <svg viewBox="0 0 16 16" aria-hidden="true"><path fill-rule="evenodd" d="M8 1 A7 7 0 1 0 8 15 A7 7 0 1 0 8 1 Z M8 2.6 C9 3.8 9.6 5.5 9.7 7.3 H6.3 C6.4 5.5 7 3.8 8 2.6 Z M6.3 8.7 H9.7 C9.6 10.5 9 12.2 8 13.4 C7 12.2 6.4 10.5 6.3 8.7 Z M2.5 7.3 C2.8 5 4.4 3.2 6.4 2.6 C5.5 3.9 5 5.5 4.9 7.3 Z M2.5 8.7 H4.9 C5 10.5 5.5 12.1 6.4 13.4 C4.4 12.8 2.8 11 2.5 8.7 Z M11.1 7.3 C11 5.5 10.5 3.9 9.6 2.6 C11.6 3.2 13.2 5 13.5 7.3 Z M11.1 8.7 H13.5 C13.2 11 11.6 12.8 9.6 13.4 C10.5 12.1 11 10.5 11.1 8.7 Z"/></svg>
      www.quillbrook.me
    </li>
    <li>
      <svg viewBox="0 0 16 16" aria-hidden="true"><path fill-rule="evenodd" d="M1 3 H15 V13 H1 Z M2.8 4.5 L8 8.6 L13.2 4.5 Z M2.5 5.8 V11.5 H13.5 V5.8 L8 10.2 Z"/></svg>
      support@quillbrook.me
    </li>
  </ul>

  <div class="person">
    <p class="person__name">Daniel Ferris</p>
    <p class="person__title">Managing Director</p>
  </div>
</section>

</body>
</html>
```